Quorva - corporate Business Card

We need a good look and innovative business card for a new start up company based in Los Angeles called "Quorva". We are in a payment business, including payment card, app, and ewallet. We are expert in online payment and Card not present (CNP) transaction.
We need an innovative, modern business card.

Our logo font is Aero Matics

Target Market(s)

Startup - Bank - Online Payment - Card Manufacturing

Industry/Entity Type

Startup

Contact Information for Business Card

phone: 555 014 7396 - Address: 4172 Marlowe blvd, Wrenhollow, OR 90299

Requirements
Must have
• Message: innovative, professional, expert, high tech, trust, online payment expert, security
Nice to have
• no comment
Should not have
• no Comment

```html
<!DOCTYPE html>
<html lang="en">
<head>
<meta charset="utf-8">
<title>Quorva — Business Card</title>
<link rel="stylesheet" href="https://fonts.googleapis.com/css2?family=Source+Sans+3:wght@400;600&display=swap">
<style>
  :root {
    --backdrop: #3a322d;
    --card-black: #0d0d0d;
    --brand-red: #c01f30;
    --text-white: #f2f2f2;
    --silver: #c4c4c4;
    --divider: #2c2c2c;
  }
  * { margin: 0; padding: 0; box-sizing: border-box; }
  html, body {
    width: 1200px; height: 900px; overflow: hidden;
    background: var(--backdrop);
    font-family: "Source Sans 3", "Myriad Pro", sans-serif;
  }
  .stage {
    width: 1200px; height: 900px;
    display: flex; align-items: center; justify-content: center; gap: 40px;
  }
  .card {
    position: relative;
    width: 540px; height: 308px;
    background: var(--card-black);
    box-shadow: 0 10px 30px rgba(0,0,0,.45);
  }
  /* Contact side */
  .brand-disc {
    position: absolute; left: 55px; top: 59px;
    width: 190px; height: 190px; border-radius: 50%;
    background: var(--brand-red);
    display: flex; align-items: center; justify-content: center;
    color: var(--card-black); font-weight: 600; font-size: 34px; letter-spacing: .5px;
  }
  .divider {
    position: absolute; left: 290px; top: 96px; bottom: 30px;
    width: 1px; background: var(--divider);
  }
  .contact {
    position: absolute; left: 318px; top: 62px;
    color: var(--text-white);
  }
  .contact__name { color: var(--brand-red); font-weight: 600; font-size: 21px; line-height: 1.05; }
  .contact__title { font-size: 14px; line-height: 1.2; }
  .contact__list { list-style: none; margin-top: 32px; font-size: 14px; line-height: 1.5; }
  .contact__list li { display: flex; align-items: center; gap: 7px; }
  .contact__list svg { width: 11px; height: 11px; fill: var(--brand-red); }
  .contact__address { margin-top: 18px; font-size: 14px; line-height: 1.35; }
  /* Brand side */
  .brand-side { display: flex; align-items: center; justify-content: center; gap: 16px; }
  .brand-side__dot { width: 92px; height: 92px; border-radius: 50%; background: #e8e8e8; }
  .brand-side__name { color: var(--silver); font-size: 60px; font-weight: 600; letter-spacing: 1px; }
</style>
</head>
<body>
<main class="stage">
  <section class="card card--contact">
    <div class="brand-disc">quorva</div>
    <div class="divider"></div>
    <div class="contact">
      <p class="contact__name">Daniel Reyes</p>
      <p class="contact__title">Managing Director</p>
      <ul class="contact__list">
        <li><svg viewBox="0 0 24 24" aria-hidden="true"><path d="M6.6 10.8a15.1 15.1 0 0 0 6.6 6.6l2.2-2.2a1 1 0 0 1 1-.25 11.4 11.4 0 0 0 3.6.57 1 1 0 0 1 1 1V20a1 1 0 0 1-1 1A17 17 0 0 1 3 4a1 1 0 0 1 1-1h3.5a1 1 0 0 1 1 1c0 1.25.2 2.45.57 3.57a1 1 0 0 1-.25 1z"/></svg>555 014 7396</li>
        <li><svg viewBox="0 0 24 24" aria-hidden="true"><circle cx="12" cy="12" r="10"/><path d="M2 12h20M12 2c3 3 3 17 0 20M12 2c-3 3-3 17 0 20" stroke="#0d0d0d" stroke-width="1.6" fill="none"/></svg>www.quorva.com</li>
      </ul>
      <p class="contact__address">4172 Marlowe blvd,<br>Wrenhollow, OR 90299</p>
    </div>
  </section>
  <section class="card brand-side">
    <span class="brand-side__dot"></span>
    <span class="brand-side__name">quorva</span>
  </section>
</main>
</body>
</html>
```